Vantoq Business Card Project showing the logo and a marbo image on the rear

Design a whacky but professional business card, the logo is for the front and the Marbo image is for the rear. Happy to consider other open source Marbo Images if the designer wants to select one from the web. Vantoq is a competitor to OMB.com.au and Pellory.com.au and is based around every property in Australia

Target Market(s)

Business

Contact Information for Business Card

Name, Title, Email, Web, Phone Number

Font styles to use
Other font styles liked:
• avenir

Requirements
Must have
• Image on Back logo on front
Nice to have
• Happy to consider other images on rear, preftably Colin Marbo. Image supplied I own, we can use open source other Marbo Images

```html
<!DOCTYPE html>
<html lang="en">
<head>
<meta charset="utf-8">
<title>Vantoq Business Card</title>
<link rel="stylesheet" href="https://fonts.googleapis.com/css2?family=Roboto:wght@400;500;700&display=swap">
<style>
  :root {
    --backdrop: #2a2a2a;
    --card: #f1f1f0;
    --ink: #141414;
    --orange: #e07b00;
    --muted: #222;
  }
  * { box-sizing: border-box; margin: 0; padding: 0; }
  html, body { width: 1200px; height: 1138px; overflow: hidden; }
  body {
    background: var(--backdrop);
    font-family: "Roboto", Arial, sans-serif;
    color: var(--ink);
    position: relative;
  }
  .card {
    position: absolute;
    background: var(--card);
    border-radius: 16px;
    overflow: hidden;
  }
  .card--front { left: 274px; top: 186px; width: 622px; height: 376px; }
  .card--back { left: 276px; top: 608px; width: 618px; height: 374px; }

  .brand { position: absolute; display: flex; align-items: center; }
  .brand__square { background: var(--orange); }
  .brand__name { font-weight: 700; color: var(--ink); line-height: 1; letter-spacing: -1px; }

  .card--front .brand { left: 170px; top: 70px; gap: 26px; }
  .card--front .brand__square { width: 58px; height: 58px; }
  .card--front .brand__name { font-size: 72px; }
  .front-url {
    position: absolute; left: 0; right: 0; top: 140px;
    text-align: center; font-size: 17px; letter-spacing: 12px; padding-left: 12px;
  }
  .city-art {
    position: absolute; left: 0; right: 0; top: 198px; bottom: 0;
    background: linear-gradient(180deg, rgba(241,241,240,0) 0%, #e4559a 22%, #d84a6a 45%, #e6c84a 72%, #7dbb3c 88%, #5ab0d6 100%);
  }

  .card--back .brand { left: 30px; top: 40px; gap: 22px; }
  .card--back .brand__square { width: 80px; height: 80px; }
  .card--back .brand__name { font-size: 80px; }
  .address { position: absolute; left: 30px; top: 164px; font-size: 16px; color: var(--muted); }
  .contacts { position: absolute; left: 30px; top: 202px; list-style: none; }
  .contacts li { display: flex; align-items: center; height: 24px; font-size: 17px; color: var(--muted); }
  .contacts svg { width: 14px; height: 14px; margin-right: 17px; }
  .accent { color: var(--orange); }
  .wave { position: absolute; left: 0; top: 0; width: 618px; height: 374px; }
  .person { position: absolute; right: 40px; top: 296px; text-align: right; }
  .person__name { font-size: 25px; font-weight: 700; line-height: 1; }
  .person__title { font-size: 16px; margin-top: 6px; }
</style>
</head>
<body>
  <section class="card card--front">
    <div class="brand">
      <span class="brand__square"></span>
      <span class="brand__name">Vantoq</span>
    </div>
    <p class="front-url">www.vantoq.com</p>
    <div class="city-art" role="img" aria-label="Colourful cartoon city skyline with a row of tram carriages"></div>
  </section>

  <section class="card card--back">
    <svg class="wave" viewBox="0 0 618 374" aria-hidden="true">
      <path d="M0 340 C150 330 250 362 380 302 C470 260 540 262 618 270 L618 374 L0 374 Z" fill="var(--orange)"/>
      <path d="M0 296 C120 340 240 350 360 300 C460 255 540 240 618 250 L618 262 C540 255 470 262 380 305 C260 362 120 355 0 318 Z" fill="var(--ink)"/>
      <path d="M60 310 C180 350 300 345 380 318 C300 354 180 360 60 310 Z" fill="var(--ink)"/>
    </svg>
    <div class="brand">
      <span class="brand__square"></span>
      <span class="brand__name">Vantoq</span>
    </div>
    <p class="address">Level 4, 18 Corvel Lane, Sydney 2000, Australia</p>
    <ul class="contacts">
      <li><svg viewBox="0 0 14 14"><circle cx="7" cy="7" r="6" fill="none" stroke="var(--orange)" stroke-width="1.5"/><path d="M4.5 4 L6 4 L6.5 6 L5.8 6.6 C6.3 7.6 6.9 8.2 7.8 8.6 L8.4 7.9 L10 8.4 L10 9.8 C7 10 4.2 7.2 4.5 4 Z" fill="var(--orange)"/></svg>(00) 4815 6270</li>
      <li><svg viewBox="0 0 14 14"><rect x="1" y="3" width="12" height="8" fill="var(--orange)"/><path d="M1 3 L7 8 L13 3" fill="none" stroke="#fff" stroke-width="1"/></svg>daskey@vantoq.com</li>
      <li><svg viewBox="0 0 14 14"><circle cx="7" cy="7" r="6" fill="var(--orange)"/><path d="M1 7 H13 M7 1 C4 4 4 10 7 13 M7 1 C10 4 10 10 7 13" fill="none" stroke="#fff" stroke-width="0.8"/></svg>www.<span class="accent">vantoq</span>.com</li>
    </ul>
    <div class="person">
      <p class="person__name">Orlen Daskey</p>
      <p class="person__title">Founder &amp; CEO</p>
    </div>
  </section>
</body>
</html>
```